Wellpath Ledgers New Website

Please review the attached Design Brief with additional details. Thank you!

The goal is to create a website that effectively communicates the benefits of WellPath Ledgers to eye care professionals. The website should streamline the process of understanding and utilizing WellPath Ledgers' services, emphasizing improved patient outcomes, increased referrals, and enhanced patient engagement.

Target Market(s)

Eyecare Professionals

Number of Pages Required

4 page

```html
<!DOCTYPE html>
<html lang="en">
<head>
<meta charset="utf-8">
<title>Wellpath Ledgers – Blog Grid</title>
<link href="https://fonts.googleapis.com/css2?family=Open+Sans:wght@400;600;700&family=Lato:wght@400;700&display=swap" rel="stylesheet">
<style>
:root{
  --ink:#1b1b2b;
  --muted:#5b5b66;
  --brand:#1f3fa8;
  --nav:#2b5f8a;
  --orange:#f8a03c;
  --night:#19112a;
  --night-soft:#2b2240;
  --card:#f4f4f4;
  --quote:#3f7e74;
  --white:#ffffff;
}
*{margin:0;padding:0;box-sizing:border-box}
html,body{width:724px;height:1200px;overflow:hidden;background:var(--white)}
body{position:relative;font-family:"Open Sans",sans-serif;color:var(--ink)}
.abs{position:absolute}

/* header */
.topbar{left:0;top:0;width:724px;height:28px;background:linear-gradient(90deg,#34466d,#273a60 60%,#3d4f74)}
.topbar-text{top:11px;font-size:6px;color:var(--white);font-weight:600;display:flex;align-items:center;gap:4px;white-space:nowrap}
.dot{width:4px;height:4px;border-radius:50%;background:var(--white);display:inline-block}
.quote-btn{left:510px;top:13px;width:67px;height:8px;background:var(--quote);color:var(--white);font-size:5.5px;font-weight:600;text-align:center;line-height:8px}
.navrow{left:0;top:28px;width:724px;height:27px;background:var(--white)}
.nav{top:37px;font-size:7px;color:#6a6a70;white-space:nowrap}
.nav.active{color:var(--nav)}
.nav.bold{color:var(--nav);font-weight:700}
.brand-mark{left:46px;top:28px;width:9px;height:9px;border-radius:50%;background:var(--orange)}
.brand-name{left:60px;top:24px;font-size:13px;font-weight:600;color:var(--brand);line-height:1;white-space:nowrap}

/* hero */
.hero{left:0;top:55px;width:724px;height:155px;background:linear-gradient(100deg,#2d4470 0%,#3f5d8f 45%,#4d6ea3 70%,#36507f 100%)}
.hero-line{left:0;top:210px;width:724px;height:2px;background:var(--orange)}
.hero-kicker{left:64px;top:113px;font-size:12px;color:var(--white)}
.hero-title{left:64px;top:130px;font-size:30px;font-weight:700;color:var(--white)}

/* blog cards */
.card{width:193px;height:269px;background:var(--card)}
.card-photo{position:absolute;left:0;top:0;width:193px;height:130px;background:linear-gradient(135deg,#c9b8a6 0%,#8ea3c8 40%,#6f87b8 60%,#d8cfc2 100%)}
.tag{position:absolute;left:4px;top:5px;height:14px;padding:0 8px;background:var(--orange);color:var(--white);font-size:7px;font-weight:600;line-height:14px;white-space:nowrap}
.date{position:absolute;left:15px;top:150px;font-size:7px;color:#666;font-weight:600;display:flex;align-items:center;gap:4px}
.title{position:absolute;left:16px;top:166px;width:176px;font-size:10.5px;font-weight:600;line-height:16px;color:var(--ink)}
.excerpt{position:absolute;left:14px;top:206px;width:176px;font-family:"Lato",sans-serif;font-size:7.7px;line-height:13.6px;color:var(--muted)}

/* footer */
.footer{left:0;top:915px;width:724px;height:285px;background:var(--night)}
.foot-name{left:72px;top:950px;font-size:18px;font-family:"Lato",sans-serif;color:var(--brand);line-height:1;white-space:nowrap}
.foot-desc{left:76px;top:987px;width:180px;font-family:"Lato",sans-serif;font-size:7.5px;line-height:13px;color:#c9c4d6}
.social{top:1032px;width:19px;height:19px;border-radius:3px;background:var(--night-soft)}
.social.on{background:var(--orange)}
.foot-head{top:945px;font-family:"Lato",sans-serif;font-weight:700;font-size:10px;color:var(--white)}
.links{top:970px;font-family:"Lato",sans-serif;font-size:7.5px;line-height:15.7px;color:#c9c4d6;list-style:none}
.news-text{left:499px;top:973px;width:160px;font-family:"Lato",sans-serif;font-size:7.5px;line-height:13px;color:#c9c4d6}
.news-input{left:499px;top:1007px;width:117px;height:29px;background:var(--white);font-family:"Lato",sans-serif;font-size:7.3px;color:#777;padding-left:15px;line-height:29px}
.news-btn{left:616px;top:1007px;width:30px;height:29px;background:var(--orange)}
.info-icon{top:1100px;width:29px;height:29px;border-radius:50%;background:var(--night-soft)}
.info-icon.on{background:var(--orange)}
.info-icon svg{position:absolute;left:7px;top:7px}
.info-head{top:1102px;font-family:"Lato",sans-serif;font-weight:700;font-size:9.5px;color:var(--white);white-space:nowrap}
.info-text{top:1117px;font-family:"Lato",sans-serif;font-size:7.3px;color:#c9c4d6;white-space:nowrap}
.divider{left:76px;top:1169px;width:572px;height:1px;background:#3a3150}
.copyright{left:0;top:1181px;width:724px;text-align:center;font-size:7.5px;color:var(--white)}
</style>
</head>
<body>

<header>
  <div class="abs topbar"></div>
  <div class="abs navrow"></div>
  <svg class="abs" style="left:0;top:13px" width="270" height="16" viewBox="0 0 270 16">
    <path d="M0 1 H235 C250 1 252 15 268 15 V16 H0Z" fill="#ffffff"/>
  </svg>
  <div class="abs topbar-text" style="left:283px"><span class="dot"></span>48 Linden Row, Brookfield, 204517</div>
  <div class="abs topbar-text" style="left:426px">Follow Us:&nbsp;<span class="dot"></span><span class="dot"></span><span class="dot"></span></div>
  <div class="abs quote-btn">GET QUOTATION</div>

  <div class="abs brand-mark"></div>
  <div class="abs brand-name">Wellpath Ledgers</div>

  <nav>
    <span class="abs nav active" style="left:271px">Home</span>
    <span class="abs nav" style="left:327px">About Us</span>
    <span class="abs nav" style="left:380px">Conditions</span>
    <span class="abs nav bold" style="left:437px">Services</span>
    <span class="abs nav" style="left:501px">Gallery</span>
    <span class="abs nav" style="left:550px">Team</span>
    <span class="abs nav" style="left:599px">Contact Us</span>
  </nav>
</header>

<section>
  <div class="abs hero" role="img" aria-label="Medical technicians working at computer screens in a lab"></div>
  <div class="abs hero-line"></div>
  <div class="abs hero-kicker">OUR BLOG</div>
  <h1 class="abs hero-title">Blog Grid</h1>
</section>

<main>
  <article class="abs card" style="left:56px;top:261px">
    <div class="card-photo" role="img" aria-label="Doctor reviewing notes with a patient in a clinic"></div>
    <span class="tag">Medical Research</span>
    <div class="date"><svg width="8" height="8" viewBox="0 0 8 8"><circle cx="4" cy="4.3" r="3" fill="none" stroke="#f8a03c" stroke-width=".8"/><path d="M4 2.8V4.4H5.2" stroke="#f8a03c" stroke-width=".7" fill="none"/></svg>January 11, 2024</div>
    <h2 class="title">The Technology Driving Patient Care Ledgers</h2>
    <p class="excerpt">Lorem ipsum dolor sit amet, consectetur adipiscing elit, sed do eiusmod tempor incididunt ut labore et dolore magna aliqua. Lorem ipsum dolor sit amet, consectetur adip</p>
  </article>
  <article class="abs card" style="left:265px;top:261px">
    <div class="card-photo" role="img" aria-label="Doctor reviewing notes with a patient in a clinic"></div>
    <span class="tag">Medical Research</span>
    <div class="date"><svg width="8" height="8" viewBox="0 0 8 8"><circle cx="4" cy="4.3" r="3" fill="none" stroke="#f8a03c" stroke-width=".8"/><path d="M4 2.8V4.4H5.2" stroke="#f8a03c" stroke-width=".7" fill="none"/></svg>January 11, 2024</div>
    <h2 class="title">The Technology Driving Patient Care Ledgers</h2>
    <p class="excerpt">Lorem ipsum dolor sit amet, consectetur adipiscing elit, sed do eiusmod tempor incididunt ut labore et dolore magna aliqua. Lorem ipsum dolor sit amet, consectetur adip</p>
  </article>
  <article class="abs card" style="left:475px;top:261px">
    <div class="card-photo" role="img" aria-label="Doctor reviewing notes with a patient in a clinic"></div>
    <span class="tag">Medical Research</span>
    <div class="date"><svg width="8" height="8" viewBox="0 0 8 8"><circle cx="4" cy="4.3" r="3" fill="none" stroke="#f8a03c" stroke-width=".8"/><path d="M4 2.8V4.4H5.2" stroke="#f8a03c" stroke-width=".7" fill="none"/></svg>January 11, 2024</div>
    <h2 class="title">The Technology Driving Patient Care Ledgers</h2>
    <p class="excerpt">Lorem ipsum dolor sit amet, consectetur adipiscing elit, sed do eiusmod tempor incididunt ut labore et dolore magna aliqua. Lorem ipsum dolor sit amet, consectetur adip</p>
  </article>
  <article class="abs card" style="left:56px;top:550px">
    <div class="card-photo" role="img" aria-label="Doctor reviewing notes with a patient in a clinic"></div>
    <span class="tag">Medical Research</span>
    <div class="date"><svg width="8" height="8" viewBox="0 0 8 8"><circle cx="4" cy="4.3" r="3" fill="none" stroke="#f8a03c" stroke-width=".8"/><path d="M4 2.8V4.4H5.2" stroke="#f8a03c" stroke-width=".7" fill="none"/></svg>January 11, 2024</div>
    <h2 class="title">The Technology Driving Patient Care Ledgers</h2>
    <p class="excerpt">Lorem ipsum dolor sit amet, consectetur adipiscing elit, sed do eiusmod tempor incididunt ut labore et dolore magna aliqua. Lorem ipsum dolor sit amet, consectetur adip</p>
  </article>
  <article class="abs card" style="left:265px;top:550px">
    <div class="card-photo" role="img" aria-label="Doctor reviewing notes with a patient in a clinic"></div>
    <span class="tag">Medical Research</span>
    <div class="date"><svg width="8" height="8" viewBox="0 0 8 8"><circle cx="4" cy="4.3" r="3" fill="none" stroke="#f8a03c" stroke-width=".8"/><path d="M4 2.8V4.4H5.2" stroke="#f8a03c" stroke-width=".7" fill="none"/></svg>January 11, 2024</div>
    <h2 class="title">The Technology Driving Patient Care Ledgers</h2>
    <p class="excerpt">Lorem ipsum dolor sit amet, consectetur adipiscing elit, sed do eiusmod tempor incididunt ut labore et dolore magna aliqua. Lorem ipsum dolor sit amet, consectetur adip</p>
  </article>
  <article class="abs card" style="left:475px;top:550px">
    <div class="card-photo" role="img" aria-label="Doctor reviewing notes with a patient in a clinic"></div>
    <span class="tag">Medical Research</span>
    <div class="date"><svg width="8" height="8" viewBox="0 0 8 8"><circle cx="4" cy="4.3" r="3" fill="none" stroke="#f8a03c" stroke-width=".8"/><path d="M4 2.8V4.4H5.2" stroke="#f8a03c" stroke-width=".7" fill="none"/></svg>January 11, 2024</div>
    <h2 class="title">The Technology Driving Patient Care Ledgers</h2>
    <p class="excerpt">Lorem ipsum dolor sit amet, consectetur adipiscing elit, sed do eiusmod tempor incididunt ut labore et dolore magna aliqua. Lorem ipsum dolor sit amet, consectetur adip</p>
  </article>
</main>

<footer>
  <svg class="abs" style="left:0;top:862px" width="724" height="56" viewBox="0 0 724 56">
    <path d="M0 48 C140 -2 300 -4 420 20 C540 44 620 40 724 24 V56 H0Z" fill="#f8a03c"/>
    <path d="M0 56 C150 12 300 10 420 34 C540 54 630 50 724 30 V56Z" fill="#19112a"/>
  </svg>
  <div class="abs footer"></div>

  <div class="abs foot-name">Wellpath Ledgers</div>
  <p class="abs foot-desc">Lorem ipsum dolor sit amet, consectetur adipiscing elit, sed do eiusmod tempor incididunt ut</p>
  <span class="abs social on" style="left:76px"></span>
  <span class="abs social" style="left:99px"></span>
  <span class="abs social" style="left:122px"></span>
  <span class="abs social" style="left:145px"></span>

  <h3 class="abs foot-head" style="left:295px">Quick Links</h3>
  <ul class="abs links" style="left:296px">
    <li>Home</li><li>Services</li><li>About Us</li><li>Contact</li><li>Blog</li><li>Testimonials</li>
  </ul>
  <ul class="abs links" style="left:377px">
    <li>Cookies Policy</li><li>Terms of Use</li><li>Careers</li><li>Our Team</li><li>More</li>
  </ul>

  <h3 class="abs foot-head" style="left:499px">Newsletters</h3>
  <p class="abs news-text">Lorem ipsum dolor sit amet, consectetur adi piscing elit, sed do eiusmod tempor</p>
  <div class="abs news-input">Enter Email Address</div>
  <div class="abs news-btn"><svg width="30" height="29" viewBox="0 0 30 29"><path d="M13 9.5L18 14.5L13 19.5" stroke="#fff" stroke-width="2.2" fill="none"/></svg></div>

  <div class="abs info-icon" style="left:76px"><svg width="15" height="15" viewBox="0 0 15 15"><path d="M7.5 1.5C5 1.5 3.5 3.3 3.5 5.5C3.5 8.5 7.5 13.5 7.5 13.5C7.5 13.5 11.5 8.5 11.5 5.5C11.5 3.3 10 1.5 7.5 1.5Z" fill="#6a5f85"/><circle cx="7.5" cy="5.5" r="1.4" fill="#2b2240"/></svg></div>
  <div class="abs info-head" style="left:115px">Address</div>
  <div class="abs info-text" style="left:114px">48 Linden Row</div>

  <div class="abs info-icon on" style="left:220px"><svg width="15" height="15" viewBox="0 0 15 15"><rect x="1.5" y="3.5" width="12" height="8" fill="#fff"/><path d="M1.5 3.5L7.5 8L13.5 3.5" stroke="#f8a03c" stroke-width=".9" fill="none"/></svg></div>
  <div class="abs info-head" style="left:259px">Email Us</div>
  <div class="abs info-text" style="left:258px">hello@wellpathledgers.com</div>

  <div class="abs info-icon" style="left:381px"><svg width="15" height="15" viewBox="0 0 15 15"><path d="M3 2L5.5 1.8L6.5 4.8L5 6C5.8 7.8 7.2 9.2 9 10L10.2 8.5L13.2 9.5L13 12C12.8 13 12 13.4 11 13.2C6.5 12.4 2.6 8.5 1.8 4C1.6 3 2 2.2 3 2Z" fill="#6a5f85"/></svg></div>
  <div class="abs info-head" style="left:420px">Contact Us</div>
  <div class="abs info-text" style="left:420px">+014(5820) 316 42</div>

  <div class="abs info-icon" style="left:518px"><svg width="15" height="15" viewBox="0 0 15 15"><circle cx="7.5" cy="7.5" r="6" fill="none" stroke="#6a5f85" stroke-width="1.1"/><path d="M7.5 4V7.8H10" stroke="#6a5f85" stroke-width="1.1" fill="none"/></svg></div>
  <div class="abs info-head" style="left:557px">Opening Hour</div>
  <div class="abs info-text" style="left:557px">Mon - Friday 10 am - 8pm</div>

  <div class="abs divider"></div>
  <div class="abs copyright">WELLPATH LEDGERS</div>
</footer>

</body>
</html>
```